Patient-centered home health care company needs a web design

We are dynamic home health care company that serves the medical and non-medical needs of our clients. We are seeking a fresh new website that incorporates our company colors - purple, teal, and tan. The site should also incorporate our logo and 'swoosh', both of which are attached. the swoosh can be recreated to make it more fresh but should have the same colors and basic concept.

The purpose of the site is to present information about our company, to present general healthcare information, and to entice visitors to provide their information or to schedule a consultation meeting (possibly through a pop up prompt). We have two existing sites - www.maplecrestcarepartners.com and www.maplecrestnursing care, both are stale and unresponsive in accordance with Googles latest algorithm changes. Would like to consolidate the two sites into one.

The home page should have a quick snapshot of our 3 main service offerings:
Maplecrest Home Health Care - private duty home caregiving
Maplecrest Nursing Care - skilled home nursing and therapy
Maplecrest Health Training School - Certified Nurse Aide Training

Each of the above services should have their own page that includes more detailed information about each.

The website should also include:
** an employment page that lists open positions and allows the applicant to fill out and submit a detailed electronic application - a copy of our paper employment is attached for reference
** the Maplecrest Health Training School page (or subpage) must include a spot for the visitor to sign up and pay for the classes online
** A Contact Us Page with contact information and a Google Map of our location

The new site must be designed to rank high in search engines, responsive to desktop, laptop, tablet, and mobile devices, and must be easy to update by our own staff through CMS. The site must be compatible with Google Analytics and common retargeting practices.

The site must have a fresh, clean, modern look but rich in content.
The site must look custom, not like a template.

Two sites that I really like the look and feel of are:
www.brivandastudio.com
www.fernholtcompanions.com

The finished product does not have to look like these, but these are good starting points.
Updates

Hoping to get some more designs. Would like to see something similiar to this site: www.fernholtcompanions.com

6b449b
01a68d
fee18a
ffffff

```html
<!DOCTYPE html>
<html lang="en">
<head>
<meta charset="utf-8">
<title>Maplecrest Home Health &amp; Skilled Care</title>
<link href="https://fonts.googleapis.com/css2?family=Roboto:ital,wght@0,300;0,400;0,500;1,400&family=Exo+2:ital,wght@1,400&display=swap" rel="stylesheet">
<style>
:root{
  --purple:#6b449b;
  --purple-dark:#4f2e7c;
  --teal:#01a68d;
  --teal-dark:#1a9a86;
  --tan:#fee18a;
  --tan-deep:#f3d27a;
  --tan-text:#5a4410;
  --white:#ffffff;
  --ink:#222222;
  --text:#555555;
  --rule:#e2e2e2;
}
*{margin:0;padding:0;box-sizing:border-box}
html,body{width:915px;height:1200px;overflow:hidden;background:var(--white)}
body{position:relative;font-family:'Roboto',sans-serif;color:var(--ink)}
.abs{position:absolute}

/* header */
.site-header{left:0;top:0;width:915px;height:91px;background:var(--white)}
.brand{left:57px;top:14px;width:150px;color:var(--ink);font-weight:400;font-size:17px;line-height:19px}
.brand .brand-name{font-size:26px;line-height:30px;display:block}
.social{left:513px;top:44px;display:flex;align-items:center;gap:6px;font-size:10.5px;color:#333}
.social .dot{width:23px;height:23px;border-radius:50%;display:inline-block}
.dot.blue{background:#2d5fa5}.dot.sky{background:#2aa6e0}.dot.orange{background:#f6921e}
.award{left:688px;top:14px;width:172px;height:64px;border-radius:6px;background:#e9eef6}

/* nav */
.main-nav{left:0;top:91px;width:915px;height:33px;background:linear-gradient(var(--purple),var(--purple-dark));
  display:flex;align-items:center;padding-left:65px;gap:16px}
.main-nav a{color:var(--white);font-size:9.6px;text-decoration:none;letter-spacing:.1px}

/* hero */
.hero{left:0;top:124px;width:915px;height:342px;overflow:hidden}
.hero-photo{left:0;top:0;width:915px;height:342px;
  background:linear-gradient(90deg,#f2f2f2 0%,#eeeeee 30%,#d9c1a6 45%,#5ba0d6 55%,#e8c8a8 70%,#d8d8d8 85%,#c7c0b8 100%)}
.hero-fade{left:0;top:0;width:450px;height:342px;background:linear-gradient(90deg,rgba(242,242,242,1) 60%,rgba(242,242,242,0))}
.hero-title{left:57px;top:70px;font-family:'Exo 2',sans-serif;font-style:italic;font-size:33px;line-height:41px;color:var(--teal)}
.hero-copy{left:57px;top:157px;width:335px;font-size:15.5px;line-height:20px;color:#222}
.hero-dots{left:57px;top:234px;display:flex;gap:4px}
.hero-dots span{width:9px;height:9px;border-radius:50%;background:#666}
.hero-dots span:first-child{background:var(--purple)}

/* service cards */
.service{top:493px;width:252px;height:178px;overflow:hidden;box-shadow:0 6px 6px -4px rgba(0,0,0,.25)}
.service .photo{left:0;top:0;width:252px;height:178px}
.service svg{left:0;top:0}
.service .badge{left:6px;top:75px;width:96px;height:96px;border-radius:50%;background:var(--white);border:3px solid #333;
  display:flex;flex-direction:column;align-items:center;justify-content:center;text-align:center;font-size:10px;line-height:12px;color:#222}
.service .badge b{font-weight:400;font-size:15px;line-height:18px}
.service .label{right:20px;top:149px;color:var(--white);font-size:12.5px;font-weight:500}
.card-school .label{color:var(--tan-text)}
.card-home{left:57px}.card-skilled{left:332px}.card-school{left:607px}

.divider{left:57px;top:705px;width:802px;height:3px;background:var(--rule)}

/* welcome */
.welcome h1{font-weight:400;font-size:21px}
.welcome{left:57px;top:729px;width:460px}
.welcome p{margin-top:10px;font-size:9.2px;line-height:16.3px;color:var(--text)}
.btn{display:inline-block;background:var(--ink);color:var(--white);font-size:9.5px;letter-spacing:.3px;padding:10px 21px;border-radius:2px}
.welcome .btn{margin-top:18px}

.testimonial{left:537px;top:733px;width:322px;height:157px;background:linear-gradient(135deg,#e6e6e6,#f4f4f4);padding:27px 18px 0 14px}
.testimonial p{font-style:italic;font-size:8.8px;line-height:16.9px;color:#333}
.testimonial .who{margin-top:3px;color:var(--teal);font-style:italic;font-size:8.8px}
.quote-mark{font-family:Georgia,serif;font-size:56px;color:#d0d0d0;line-height:1}

/* panels */
.panel{top:912px;height:197px;background:var(--white);border:1px solid #dddddd;box-shadow:0 1px 3px rgba(0,0,0,.08)}
.panel svg{left:-1px;top:-1px}
.panel h2{left:16px;top:8px;color:var(--white);font-weight:400;font-size:17px}
.news{left:57px;width:390px}
.join{left:468px;width:391px}
.news-item{left:17px;width:355px;font-size:9.2px;line-height:16.4px;color:var(--text)}
.news-item .date{font-weight:500;color:#3a2a60;font-size:10px}
.news-item a{color:var(--teal);text-decoration:none}
.join .photo{left:14px;top:54px;width:145px;height:126px;background:linear-gradient(135deg,#8b6c52,#c9b59c 45%,#5f7fbf 75%,#3b4f8a)}
.join .copy{left:173px;top:54px;width:205px;font-size:9.2px;line-height:16.4px;color:var(--text)}
.join .btn{position:absolute;left:173px;top:150px}

/* footer */
.site-footer{left:0;top:1125px;width:915px;height:75px;background:linear-gradient(var(--tan-deep),var(--tan))}
.footer-links{left:0;top:22px;width:915px;text-align:center;font-size:9.5px;color:#333}
.footer-links span{margin:0 6px;color:#555}
.copyright{left:0;top:45px;width:915px;text-align:center;font-size:8px;color:#555}
</style>
</head>
<body>

<header class="site-header abs">
  <div class="brand abs"><span class="brand-name">Maplecrest</span>Home Health &amp;<br>Skilled Care</div>
  <div class="social abs">Find Us On:<span class="dot blue"></span><span class="dot sky"></span><span class="dot orange"></span></div>
  <div class="award abs" role="img" aria-label="Small business of the year award badge"></div>
</header>

<nav class="main-nav abs">
  <a>HOME</a><a>ABOUT US</a><a>NURSING SERVICES</a><a>HOME HEALTH AIDES</a><a>MAPLECREST HEALTH TRAINING SCHOOL</a><a>NEWS &amp; RESOURCES</a><a>JOIN OUR TEAM</a><a>CONTACT US</a>
</nav>

<section class="hero abs">
  <div class="hero-photo abs" role="img" aria-label="Photo of a smiling nurse in blue scrubs with an older woman"></div>
  <div class="hero-fade abs"></div>
  <div class="hero-title abs">Serving With Integrity<br>and Compassion</div>
  <p class="hero-copy abs">We strive to improve the health of our clients in a manner that distinguishes us in our industry.</p>
  <div class="hero-dots abs"><span></span><span></span><span></span><span></span></div>
</section>

<article class="service card-home abs">
  <div class="photo abs" role="img" aria-label="Photo of a caregiver with a smiling elderly woman" style="background:linear-gradient(135deg,#7a5a3e,#d9b98f 50%,#a7bfd6)"></div>
  <svg class="abs" width="252" height="178"><path d="M0 130 C90 118 170 120 252 108 L252 178 L0 178Z" fill="var(--purple)"/></svg>
  <div class="badge abs"><b>Maplecrest</b>Home Health<br>Care</div>
  <div class="label abs">Home Health Care</div>
</article>

<article class="service card-skilled abs">
  <div class="photo abs" role="img" aria-label="Photo of a nurse visiting an older woman at home" style="background:linear-gradient(135deg,#6b4a36,#3f5a3a 40%,#c98f8a 75%,#8a6a4e)"></div>
  <svg class="abs" width="252" height="178"><path d="M0 130 C90 118 170 120 252 108 L252 178 L0 178Z" fill="var(--teal-dark)"/></svg>
  <div class="badge abs"><b>Maplecrest</b>Skilled Care</div>
  <div class="label abs">Skilled Care</div>
</article>

<article class="service card-school abs">
  <div class="photo abs" role="img" aria-label="Photo of a group of healthcare professionals" style="background:linear-gradient(135deg,#f4f4f4,#d8c2ae 40%,#6fa3c7 70%,#f0f0f0)"></div>
  <svg class="abs" width="252" height="178"><path d="M0 130 C90 118 170 120 252 108 L252 178 L0 178Z" fill="var(--tan)"/></svg>
  <div class="badge abs"><b>Maplecrest</b>Health Training<br>School</div>
  <div class="label abs">Health Training School</div>
</article>

<div class="divider abs"></div>

<section class="welcome abs">
  <h1>Welcome to Our Website</h1>
  <p>Aliquam molestie, mi et imperdiet euismod, dui purus auctor tellus, et interdum lacus lectus et ante. Sed accumsan sollicitudin sapien, sit amet adipiscing turpis gravida ac. In congue, neque ac lobortis volutpat, libero mauris varius mi, vitae suscipit ipsum ligula vitae risus. Duis aliquam nibh a dui iaculis viverra id a velit. Vivamus egestas risus in magna varius commodo. Sed semper viverra egestas. Etiam pretium porttitor lectus, vel ornare neque porta volutpat.</p>
  <span class="btn">READ MORE</span>
</section>

<aside class="testimonial abs">
  <span class="quote-mark abs" style="left:6px;top:-6px">&ldquo;</span>
  <span class="quote-mark abs" style="right:6px;top:112px">&rdquo;</span>
  <p>Thank you all so much for everything you did to put together my schedule of care for the July 4th weekend.&nbsp; Things can be rather difficult for a disabled person away from home, but you all made a HUGE difference!&nbsp; The aide was very experienced, very professional and courteous.&nbsp; I couldn't have asked for better care!&nbsp; If only she lived in Georgia...I would hire her myself!</p>
  <div class="who">--Dana</div>
</aside>

<section class="panel news abs">
  <svg class="abs" width="392" height="42"><path d="M0 0 H392 V20 C300 14 150 22 60 40 C30 46 10 40 0 36Z" fill="var(--purple)"/></svg>
  <h2 class="abs">News &amp; Resources</h2>
  <div class="news-item abs" style="top:50px"><div class="date">May 01, 2015</div>Aliquam molestie, mi et imperdiet euismod, dui purus auctor tellus, et interdum lacus lectus et ante. Sed accumsan sollicitudin sapien, sit amet adipiscing turpis gravida ac...<a>Read More</a></div>
  <div class="news-item abs" style="top:124px"><div class="date">May 01, 2015</div>Aliquam molestie, mi et imperdiet euismod, dui purus auctor tellus, et interdum lacus lectus et ante. Sed accumsan sollicitudin sapien, sit amet adipiscing turpis gravida ac...<a>Read More</a></div>
</section>

<section class="panel join abs">
  <svg class="abs" width="393" height="42"><path d="M0 0 H393 V20 C300 14 150 22 60 40 C30 46 10 40 0 36Z" fill="var(--teal-dark)"/></svg>
  <h2 class="abs">Join Our Team</h2>
  <div class="photo abs" role="img" aria-label="Photo of a caregiver with an elderly woman in a wheelchair"></div>
  <p class="copy abs">Aliquam molestie, mi et imperdiet euismod, dui purus auctor tellus, et interdum lacus lectus et ante. Sed accumsan sollicitudin sapien, sit amet adipiscing turpis gravida ac. Suspendisse lobortis turpis in odio blandit ac interdum..</p>
  <span class="btn">READ MORE</span>
</section>

<footer class="site-footer abs">
  <div class="footer-links abs">Home<span>/</span>About Us<span>/</span>Nursing Services<span>/</span>Home Health Aides<span>/</span>Maplecrest Health Training School<span>/</span>News &amp; Resources<span>/</span>Join Our Team<span>/</span>Contact Us</div>
  <div class="copyright abs">Copyright ©2015&nbsp; Maplecrest Home Health Care.All Right Reserved</div>
</footer>

</body>
</html>
```